Header Card Design for Marine Tool Product

We package up our small tools in bags. A nice header card would finish the look.
* Bag is 4" wide. Header Card should be 4x4, folded to 4x2
* Back of card should have 2.25x1.25 area for our part number sticker.
* Design to reinforce the brand and add (perception of) quality to the product.

Brand Website: harbolvex.com

Target Market(s)

Boat Mechanics/Boat owners

Industry/Entity Type

```html
<!DOCTYPE html>
<html lang="en">
<head>
<meta charset="utf-8">
<title>Harbolvex Header Card</title>
<link rel="stylesheet" href="https://fonts.googleapis.com/css2?family=Oswald:wght@600;700&family=Roboto+Condensed:wght@300;400&family=Roboto+Mono:wght@700&display=swap">
<style>
  :root {
    --paper: #ffffff;
    --frame: #9a9a9a;
    --ink: #1a1a1a;
    --white: #ffffff;
    --red-edge: #d62a1e;
    --red-orange: #dc3b1c;
    --red-mid: #9a2620;
    --maroon: #5e1a1c;
    --dark-center: #2a1d1e;
  }
  * { margin: 0; padding: 0; box-sizing: border-box; }
  html, body {
    width: 1188px; height: 1200px; overflow: hidden; background: var(--paper);
  }
  .sheet {
    position: relative; width: 1188px; height: 1200px;
    border: 1px solid var(--frame); background: var(--paper);
  }
  .panel-label {
    position: absolute; left: 0; width: 100%; text-align: center;
    font-family: Arial, Helvetica, sans-serif; font-size: 30px; color: var(--ink);
  }
  .panel-label--back { top: 64px; transform: rotate(180deg); }
  .panel-label--front { top: 1100px; }
  .card {
    position: absolute; left: 106px; top: 113px; width: 977px; height: 977px;
    background: linear-gradient(90deg,
      var(--red-edge) 0%, var(--red-orange) 8%, var(--red-edge) 16%,
      var(--red-mid) 28%, var(--maroon) 42%, var(--dark-center) 50%,
      var(--maroon) 60%, var(--red-mid) 74%, var(--red-edge) 88%, var(--red-orange) 96%, var(--red-edge) 100%);
  }
  .card__fold {
    position: absolute; left: 0; top: 488px; width: 100%; height: 1px; background: var(--white);
  }
  .back-panel {
    position: absolute; left: 0; top: 0; width: 977px; height: 488px;
    transform: rotate(180deg); color: var(--white);
  }
  .brand-mark {
    position: absolute; background: var(--white);
  }
  .brand-name {
    position: absolute; font-family: "Oswald", sans-serif; font-weight: 700;
    color: var(--white); text-transform: uppercase; line-height: 1; white-space: nowrap;
  }
  .back-panel .brand-mark { left: 38px; top: 165px; width: 66px; height: 66px; }
  .back-panel .brand-name { left: 128px; top: 172px; font-size: 46px; letter-spacing: 0; }
  .contact { position: absolute; left: 38px; white-space: nowrap; color: var(--white); }
  .contact--address {
    top: 270px; font-family: "Roboto Condensed", sans-serif; font-weight: 400;
    font-size: 27px; line-height: 30px;
  }
  .contact--phone {
    top: 360px; font-family: "Roboto Condensed", sans-serif; font-weight: 300;
    font-size: 34px; letter-spacing: 9px;
  }
  .contact--web {
    top: 427px; font-family: "Roboto Mono", monospace; font-weight: 700;
    font-size: 21px; letter-spacing: 6px;
  }
  .front-panel {
    position: absolute; left: 0; top: 489px; width: 977px; height: 488px; color: var(--white);
  }
  .front-panel .brand-mark { left: 150px; top: 200px; width: 150px; height: 150px; }
  .front-panel .brand-name { left: 373px; top: 207px; font-size: 97px; letter-spacing: 0; }
  .tagline {
    position: absolute; left: 373px; top: 357px; font-family: "Oswald", sans-serif;
    font-weight: 600; font-size: 31px; color: var(--white); white-space: nowrap; letter-spacing: 0.6px;
  }
  .die-lines { position: absolute; left: 0; top: 0; width: 1188px; height: 1200px; pointer-events: none; }
  .die-lines path, .die-lines rect { fill: none; stroke: var(--white); stroke-width: 3; }
</style>
</head>
<body>
  <div class="sheet">
    <div class="panel-label panel-label--back">BACK</div>

    <div class="card">
      <section class="back-panel" aria-label="Back of header card">
        <div class="brand-mark"></div>
        <div class="brand-name">Harbolvex</div>
        <p class="contact contact--address">1480 Tidewater Rd, Suite 112<br>Charleston&nbsp;&nbsp;&nbsp; SC,&nbsp;&nbsp; 29990</p>
        <p class="contact contact--phone">(555) 014-2387</p>
        <p class="contact contact--web">www.harbolvex.com</p>
      </section>

      <div class="card__fold"></div>

      <section class="front-panel" aria-label="Front of header card">
        <div class="brand-mark"></div>
        <div class="brand-name">Harbolvex</div>
        <p class="tagline">Born in Charleston, South Carolina</p>
      </section>
    </div>

    <svg class="die-lines" viewBox="0 0 1188 1200" aria-hidden="true">
      <rect class="sticker-area" x="142" y="150" width="550" height="306" rx="12"/>
      <path class="hang-hole hang-hole--back" d="M520 491 H668 A21 21 0 0 1 668 533 H622 Q618 533 617 536 A25 25 0 0 1 571 536 Q570 533 566 533 H520 A21 21 0 0 1 520 491 Z"/>
      <path class="hang-hole hang-hole--front" d="M520 669 H566 Q570 669 571 666 A25 25 0 0 1 617 666 Q618 669 622 669 H668 A21 21 0 0 1 668 711 H520 A21 21 0 0 1 520 669 Z"/>
    </svg>

    <div class="panel-label panel-label--front">FRONT</div>
  </div>
</body>
</html>
```